Corvane Spectrix Holdings - Business Cards

I would like a design developed using the logo (number 60387519) previously developed and attached. The information needs to include everything shown on the attached email title block, arranged to suit a business format. I would like a white background, with no other graphics added.
I need an editable version (e.g. MSWord) so I can change the name shown on the business card for others.

Target Market(s)

Mining & Heavy Manufacturing industries

Industry/Entity Type

Mining

Contact Information for Business Card

Refer to attached email title block in MSWord format for the details to be included.

Colors

Designer to choose colors to be used in the design.

Requirements
Must have
• White background, and fonts and text colour to match the unique font in the logo.
Nice to have
• the website address to be shown along the bottom of the card, as it is quite long.
Should not have
• Dark background, or unnecessary graphics

```html
<!DOCTYPE html>
<html lang="en">
<head>
<meta charset="utf-8">
<title>Corvane Spectrix Holdings – Business Card</title>
<link rel="stylesheet" href="https://fonts.googleapis.com/css2?family=Roboto:wght@300;400;700&display=swap">
<style>
  :root {
    --brand-blue: #1f6fb2;
    --text-grey: #555a5f;
    --paper: #ffffff;
    --shadow: rgba(0, 0, 0, 0.28);
  }
  * { margin: 0; padding: 0; box-sizing: border-box; }
  html, body { width: 1200px; height: 686px; overflow: hidden; background: var(--paper); }
  .card {
    position: relative;
    width: 1200px;
    height: 686px;
    background: var(--paper);
    font-family: "Roboto", Arial, sans-serif;
    color: var(--text-grey);
  }
  .person-name {
    position: absolute; left: 54px; top: 62px;
    font-size: 47px; font-weight: 700; color: var(--brand-blue);
    letter-spacing: 0.2px;
  }
  .person-role {
    position: absolute; left: 54px; top: 124px;
    font-size: 31px; font-weight: 300;
  }
  .contact-list { position: absolute; left: 54px; top: 226px; list-style: none; }
  .contact-item {
    display: flex; align-items: center; height: 52px;
    font-size: 32px; font-weight: 300;
  }
  .contact-icon { width: 30px; height: 30px; margin-right: 26px; flex: none; }
  .divider {
    position: absolute; left: 130px; width: 880px; height: 18px;
    background: radial-gradient(ellipse at center, var(--shadow) 0%, rgba(0,0,0,0.08) 45%, rgba(0,0,0,0) 72%);
  }
  .divider-top { top: 418px; }
  .divider-bottom { top: 638px; }
  .brand-mark {
    position: absolute; left: 52px; top: 490px;
    display: flex; align-items: center; gap: 18px;
  }
  .brand-dot { width: 58px; height: 58px; border-radius: 50%; background: var(--brand-blue); flex: none; }
  .brand-name {
    font-size: 33px; font-weight: 700; color: var(--brand-blue);
    line-height: 1.1; letter-spacing: 1px; text-transform: uppercase;
  }
  .company-details { position: absolute; left: 516px; top: 446px; list-style: none; }
  .detail-item {
    display: flex; align-items: flex-start;
    font-size: 32px; font-weight: 300; line-height: 38px; margin-bottom: 10px;
  }
  .detail-item .contact-icon { width: 28px; height: 28px; margin: 5px 14px 0 0; }
  .detail-item.no-icon { padding-left: 42px; }
</style>
</head>
<body>
<main class="card">
  <h1 class="person-name">Marcello (Marc) Venturi</h1>
  <p class="person-role">Director</p>

  <ul class="contact-list">
    <li class="contact-item">
      <svg class="contact-icon" viewBox="0 0 24 24" aria-hidden="true">
        <path d="M2 9 L12 3 L22 9 V21 H2 Z" fill="var(--brand-blue)"/>
        <path d="M2 9 L12 15 L22 9" fill="none" stroke="#fff" stroke-width="1.6"/>
      </svg>
      Email: marcello.venturi@corvanespectrix.com.au
    </li>
    <li class="contact-item">
      <svg class="contact-icon" viewBox="0 0 24 24" aria-hidden="true">
        <rect x="6" y="1.5" width="12" height="21" rx="2.5" fill="var(--brand-blue)"/>
        <rect x="8" y="4.5" width="8" height="12" fill="#fff"/>
        <circle cx="12" cy="19.3" r="1.3" fill="#fff"/>
      </svg>
      Phone: +61 400 382 715
    </li>
    <li class="contact-item">
      <svg class="contact-icon" viewBox="0 0 24 24" aria-hidden="true">
        <path d="M3 5 H21 V16 H10 L5 20 V16 H3 Z" fill="var(--brand-blue)"/>
      </svg>
      Chat: cvs.marcello.venturi
    </li>
  </ul>

  <div class="divider divider-top"></div>

  <div class="brand-mark">
    <span class="brand-dot"></span>
    <span class="brand-name">Corvane Spectrix<br>Holdings</span>
  </div>

  <ul class="company-details">
    <li class="detail-item">
      <svg class="contact-icon" viewBox="0 0 24 24" aria-hidden="true">
        <path d="M12 1.5 C7.6 1.5 4.5 4.7 4.5 8.8 C4.5 14 12 21 12 21 C12 21 19.5 14 19.5 8.8 C19.5 4.7 16.4 1.5 12 1.5 Z" fill="var(--brand-blue)"/>
        <circle cx="12" cy="8.8" r="3" fill="#fff"/>
        <ellipse cx="12" cy="21.5" rx="6" ry="1.5" fill="none" stroke="var(--brand-blue)" stroke-width="1.2"/>
      </svg>
      <span>PO BOX 47, Carrington<br>NSW 2294, AUSTRALIA</span>
    </li>
    <li class="detail-item">
      <svg class="contact-icon" viewBox="0 0 24 24" aria-hidden="true">
        <circle cx="12" cy="12" r="10" fill="var(--brand-blue)"/>
        <path d="M7 7 C9 6 10 8 9 10 C8 12 11 13 11 16 M14 4 C15 7 18 7 19 9 M15 14 C17 13 18 15 17 18" fill="none" stroke="#fff" stroke-width="1.6" stroke-linecap="round"/>
      </svg>
      www.corvanespectrixholdings.com.au
    </li>
    <li class="detail-item no-icon">ABN 48 302 715 964</li>
  </ul>

  <div class="divider divider-bottom"></div>
</main>
</body>
</html>
```